MV Decor

There is a sample provided with the arabic text of the business card. please copy paste the same text and the same Logo (The two triangles) Just try to incorproate the Brown background attached (you are free to change the colors) Id like the colors to be mainly shades of black and red.

```html
<!DOCTYPE html>
<html lang="ar">
<head>
<meta charset="utf-8">
<title>MV Decor — Business Card</title>
<link rel="stylesheet" href="https://fonts.googleapis.com/css2?family=Cairo:wght@300;400;700&family=Aref+Ruqaa:wght@400;700&family=Roboto:wght@400&display=swap">
<style>
  :root {
    --page-bg: #4a2c1c;
    --card-red: #cc2245;
    --card-red-light: #d8345a;
    --card-red-deep: #b81a3a;
    --ink-light: #ffffff;
    --rule: rgba(255,255,255,0.75);
  }
  * { margin: 0; padding: 0; box-sizing: border-box; }
  html, body { width: 1125px; height: 1200px; overflow: hidden; }
  body { background: var(--page-bg); position: relative; font-family: "Cairo", sans-serif; }

  .card {
    position: absolute;
    left: 171px;
    width: 825px;
    height: 472px;
    background: var(--card-red);
    overflow: hidden;
  }
  .card--front { top: 106px; }
  .card--back { top: 639px; }

  .card__texture {
    position: absolute; inset: 0;
    background:
      radial-gradient(ellipse at 45% 35%, var(--card-red-light) 0%, rgba(216,52,90,0) 60%),
      linear-gradient(180deg, var(--card-red) 0%, var(--card-red-deep) 100%);
  }

  .brand-name {
    position: absolute;
    left: 130px; width: 230px;
    text-align: center;
    font-family: "Cairo", sans-serif;
    font-weight: 700;
    font-size: 42px;
    letter-spacing: 2px;
    color: var(--ink-light);
    line-height: 1;
  }
  .card--front .brand-name { top: 200px; }
  .card--back .brand-name { top: 318px; }

  .divider {
    position: absolute;
    left: 396px; top: 95px;
    width: 1px; height: 253px;
    background: var(--rule);
  }

  .contact {
    position: absolute;
    right: 148px; top: 92px;
    width: 250px;
    direction: rtl;
    text-align: right;
    color: var(--ink-light);
  }
  .contact__name {
    font-family: "Aref Ruqaa", serif;
    font-weight: 700;
    font-size: 27px;
    line-height: 1.3;
    text-align: center;
  }
  .contact__title {
    font-family: "Aref Ruqaa", serif;
    font-size: 17px;
    line-height: 1.3;
    text-align: center;
  }
  .credentials {
    list-style: none;
    margin-top: 18px;
    font-weight: 300;
    font-size: 22px;
    line-height: 29px;
  }
  .phone {
    direction: ltr;
    display: flex;
    justify-content: flex-end;
    align-items: center;
    gap: 6px;
    margin-top: 24px;
    font-family: "Roboto", sans-serif;
    font-size: 21px;
  }
  .phone svg { width: 18px; height: 18px; fill: var(--ink-light); }

  .services {
    position: absolute;
    right: 124px; top: 100px;
    width: 300px;
    direction: rtl;
    list-style: none;
    color: var(--ink-light);
    font-weight: 300;
    font-size: 24px;
    line-height: 33px;
  }
  .services li { position: relative; padding-left: 22px; }
  .services li::after {
    content: "";
    position: absolute;
    left: 0; top: 15px;
    width: 8px; height: 8px;
    border-radius: 50%;
    background: var(--ink-light);
  }
</style>
</head>
<body>

<section class="card card--front">
  <div class="card__texture" role="img" aria-label="Soft red mosaic pattern of small squares and dots"></div>
  <div class="brand-name">MV DECOR</div>
  <div class="divider"></div>
  <div class="contact">
    <p class="contact__name">المهندس / سامي ناصر الحداد</p>
    <p class="contact__title">أستاذ جامعي</p>
    <ul class="credentials">
      <li>ماجستير هندسة ديكور</li>
      <li>دبلوم عالي فن تشكيلي</li>
      <li>جامعة الرواق (فالين)</li>
      <li>استشارات هندسية-فنية</li>
    </ul>
    <p class="phone">
      <svg viewBox="0 0 24 24" aria-hidden="true"><path d="M6.6 10.8c1.4 2.8 3.8 5.1 6.6 6.6l2.2-2.2c.3-.3.7-.4 1-.2 1.1.4 2.3.6 3.6.6.6 0 1 .4 1 1V20c0 .6-.4 1-1 1C10.6 21 3 13.4 3 4c0-.6.4-1 1-1h3.5c.6 0 1 .4 1 1 0 1.3.2 2.5.6 3.6.1.3 0 .7-.2 1l-2.3 2.2z"/></svg>
      39004512 / 66008294
    </p>
  </div>
</section>

<section class="card card--back">
  <div class="card__texture" role="img" aria-label="Soft red mosaic pattern of small squares and dots"></div>
  <div class="brand-name">MV DECOR</div>
  <ul class="services">
    <li>ماجستير هندسة ديكور</li>
    <li>دبلوم عالي فن تشكيلي</li>
    <li>جامعة الرواق (فالين)</li>
    <li>استشارات هندسية-فنية</li>
    <li>ماجستير هندسة ديكور</li>
    <li>دبلوم عالي فن تشكيلي</li>
    <li>جامعة الرواق (فالين)</li>
    <li>استشارات هندسية-فنية</li>
  </ul>
</section>

</body>
</html>
```